Verodex business card

Business card for sustainable investment company called "Verodex". Verodex is an exchange platform selling carbon credits between buyers and sellers. Carbon Credits are an environmental commodity for reducing global carbon emissions.

the card should obviously have our logo and the theme should be sustainability/environment mixed with a trading platform.

Contact Information for Business Card

Logo, Name, Title, Phone, Email

Colors
0054AA
0677BA
7BADD7
CADEEF
E8F1F8
0094D4
00A9DD
6FCCEA
C7EBF8
E9F6FB
00AB8E
00BBA5
67D7C9
C6EFE9
E9F9F6
59FF00
82FF00
B8FF75
E3FFCB
F4FFEA

```html
<!DOCTYPE html>
<html lang="en">
<head>
<meta charset="utf-8">
<title>Verodex business card</title>
<link rel="stylesheet" href="https://fonts.googleapis.com/css2?family=Open+Sans:wght@400;600;700;800&display=swap">
<style>
  :root {
    --backdrop: #d9dde1;
    --card: #1e1f23;
    --card-deep: #16171a;
    --text-light: #ffffff;
    --text-soft: #e6e8ea;
    --accent: #0094d4;
    --accent-light: #6fccea;
    --decor: #26272c;
  }
  * { margin: 0; padding: 0; box-sizing: border-box; }
  html, body { width: 1200px; height: 780px; overflow: hidden; }
  body {
    background: var(--backdrop);
    font-family: "Open Sans", Arial, sans-serif;
    display: flex;
    flex-direction: column;
    align-items: center;
    justify-content: center;
    gap: 40px;
  }
  .card {
    position: relative;
    width: 560px;
    height: 320px;
    border-radius: 22px;
    background: var(--card);
    overflow: hidden;
    box-shadow: 0 10px 24px rgba(0,0,0,.25);
  }
  .cards { display: flex; gap: 40px; }

  /* front */
  .brand { position: absolute; left: 30px; top: 28px; display: flex; align-items: center; gap: 12px; }
  .brand-mark { width: 26px; height: 26px; background: var(--accent); border-radius: 4px; }
  .brand-name { color: var(--text-light); font-weight: 700; font-size: 30px; letter-spacing: 1px; text-transform: uppercase; }

  .person { position: absolute; right: 40px; top: 34px; text-align: right; }
  .person-name { color: var(--accent-light); font-weight: 800; font-size: 26px; line-height: 1.1; }
  .person-title { color: var(--text-light); font-weight: 400; font-size: 15px; margin-top: 4px; letter-spacing: .5px; }
  .accent-bar {
    position: absolute; right: 0; top: 34px; width: 16px; height: 58px;
    background: linear-gradient(180deg, var(--accent-light), var(--accent));
  }

  .contact { position: absolute; left: 30px; bottom: 28px; color: var(--text-soft); font-size: 13px; line-height: 1.45; }
  .contact-address { margin-bottom: 6px; }
  .contact-row { display: flex; align-items: center; gap: 7px; }
  .contact-row svg { width: 12px; height: 12px; fill: var(--accent); flex: none; }

  .watermark {
    position: absolute; right: -6px; bottom: 18px;
    color: var(--decor); font-weight: 800; font-size: 78px;
    text-transform: uppercase; letter-spacing: 1px; line-height: 1;
  }

  /* back */
  .back-pattern {
    position: absolute; inset: 0;
    background: linear-gradient(120deg, var(--card-deep) 0%, var(--card) 55%, #55585e 85%, #b9bcc0 100%);
  }
  .back-brand {
    position: absolute; left: 50%; top: 50%; transform: translate(-50%, -50%);
    color: var(--accent); font-weight: 700; font-size: 30px;
    text-transform: uppercase; letter-spacing: 1px;
  }
</style>
</head>
<body>
  <div class="cards">
    <section class="card card-front">
      <div class="brand">
        <span class="brand-mark"></span>
        <span class="brand-name">Verodex</span>
      </div>

      <div class="person">
        <div class="person-name">Lena Marovic</div>
        <div class="person-title">Managing Director</div>
      </div>
      <div class="accent-bar"></div>

      <div class="watermark">Verodex</div>

      <div class="contact">
        <div class="contact-address">4180 Harbor Ln. Suite 310<br>Dayton, OH 45402</div>
        <div class="contact-row">
          <svg viewBox="0 0 24 24"><path d="M6.6 10.8a15.1 15.1 0 0 0 6.6 6.6l2.2-2.2c.3-.3.7-.4 1-.2 1.1.4 2.3.6 3.6.6.6 0 1 .4 1 1V20c0 .6-.4 1-1 1A17 17 0 0 1 3 4c0-.6.4-1 1-1h3.5c.6 0 1 .4 1 1 0 1.3.2 2.5.6 3.6.1.3 0 .7-.2 1z"/></svg>
          <span>(555) 214-0387</span>
        </div>
        <div class="contact-row">
          <svg viewBox="0 0 24 24"><path d="M2 5h20v14H2z M4 7v.5l8 5 8-5V7l-8 5z"/></svg>
          <span>info@verodex.com</span>
        </div>
        <div class="contact-row">
          <svg viewBox="0 0 24 24"><circle cx="12" cy="12" r="10"/></svg>
          <span>www.verodex.com</span>
        </div>
      </div>
    </section>

    <section class="card card-back">
      <div class="back-pattern" role="img" aria-label="Repeating brand pattern on dark ground with a silver sheen toward the right edge"></div>
      <div class="back-brand">Verodex</div>
    </section>
  </div>
</body>
</html>
```